3D abstract logo Construction, Kitchen and Bath design and Project Management Business Card Design

I want a 3d abstract logo for a new General Construction, Kitchen and Bath design and Project Management Company located at Philadelphia PA, we want to put our logo in the white color trucks too. I want to look professional and serious at the same time look like an architect design and the warm originals color that make you feel in a nice decorated home, I like the colors trend in this link:
http://www.quellmark.example/qm/ggs/pageeditor.aspx?alt_doc_id=RT41K-M9B33-2W5&doc_id=5913046628&pf_id=D4H

I was thinking about a roof and the PA font could have square shape or like wood framing with two tones of the brick color black and creamy yellow color.... Also I like the keystone Idea like the modification or the Ridgeline Parkway logo but curvy at the top

The final design should communicate big company (because we want to grow), responsible, professional and organized that really care about our customers and give them everything they need... plan and design, excellent labor and Project Management
Updates

I doesn't have to be 3d

Reason: I haven't received enough options...

Please stick with the warm tones shown in the image001 attached I like spicy cinnamon instead a cold wine or brick color and also the cream yellowish tones added

Hello designers, please use only the idea and colors of the image001 I don't want to be stick with a house logo because I do commercial construction too so I prefer work around the keystone idea maybe leaving the style of the PA.
I'd like the base tone on the card dark like first option and you can send me a white option too.

Please send me your ideas as soon as possible 

Thank you so much!

Target Market(s)

Builders, State, commercial business owners, Property owners or Real State and Property Management Companies

Industry/Entity Type

Architect

Contact Information for Business Card

RK Buildworks LLC
“Your project is our business”
Lorna Vasquel Eng.
President
Commercial & Residential General Construction
Kitchen & Bath Design | Project Management
Phone: 555-304-7718 | Fax: 555-304-7719 Cell: 555-862-3097
lorna@rkbuildworks.example

```html
<!DOCTYPE html>
<html lang="en">
<head>
<meta charset="utf-8">
<title>RK Buildworks — Business Card</title>
<link rel="stylesheet" href="https://fonts.googleapis.com/css2?family=PT+Sans:ital,wght@0,400;0,700;1,400&display=swap">
<style>
  :root {
    --cinnamon: #7a2121;
    --cinnamon-deep: #661a1a;
    --cream: #e8c98c;
    --cream-light: #f0d9a6;
    --rose-line: #b57264;
    --backdrop: #e9e5df;
    --card-shadow: rgba(40, 20, 10, 0.25);
  }
  * { box-sizing: border-box; margin: 0; padding: 0; }
  html, body { width: 1200px; height: 865px; overflow: hidden; }
  body {
    background: var(--backdrop);
    font-family: "PT Sans", Verdana, sans-serif;
    position: relative;
  }
  .card {
    position: absolute;
    left: 270px;
    width: 660px;
    height: 377px;
    border-radius: 4px;
    overflow: hidden;
    box-shadow: 0 6px 18px var(--card-shadow);
  }
  /* Back side */
  .card--back { top: 36px; background: var(--cinnamon); }
  .brand-circle {
    position: absolute;
    left: 150px; top: 88px;
    width: 200px; height: 200px;
    border-radius: 50%;
    background: var(--cream);
    display: flex; align-items: center; justify-content: center;
  }
  .brand-name {
    color: var(--cinnamon);
    font-weight: 700;
    font-size: 28px;
    text-align: center;
    line-height: 1.1;
  }
  .back-text {
    position: absolute;
    left: 390px; top: 150px;
    color: var(--cream);
  }
  .tagline { font-size: 22px; margin-bottom: 28px; }
  .website { font-size: 15px; letter-spacing: 0.5px; }

  /* Front side */
  .card--front { top: 450px; background: var(--cream); }
  .front-art { position: absolute; inset: 0; }
  .person { position: absolute; left: 36px; top: 30px; color: var(--cinnamon); }
  .person-name { font-size: 36px; font-weight: 700; letter-spacing: 1px; line-height: 1; }
  .person-title { font-size: 20px; font-style: italic; margin-top: 4px; }
  .services { font-size: 19px; line-height: 1.15; margin-top: 16px; width: 430px; }
  .contacts {
    position: absolute; left: 36px; top: 218px;
    display: grid; grid-template-columns: 90px auto; row-gap: 8px;
    color: var(--cinnamon); font-size: 15px;
  }
  .contact-label { font-size: 14px; }
  .front-brand {
    position: absolute;
    left: 520px; top: 252px;
    width: 118px; height: 118px;
    border-radius: 50%;
    background: var(--cream);
    display: flex; align-items: center; justify-content: center;
  }
  .front-brand .brand-name { font-size: 17px; }
</style>
</head>
<body>

<section class="card card--back" aria-label="Business card back">
  <div class="brand-circle"><span class="brand-name">RK<br>Buildworks</span></div>
  <div class="back-text">
    <p class="tagline">Your project is our business</p>
    <p class="website">www.rkbuildworks.example</p>
  </div>
</section>

<section class="card card--front" aria-label="Business card front">
  <svg class="front-art" width="660" height="377" viewBox="0 0 660 377" aria-hidden="true">
    <path d="M660 90 C 560 100, 610 300, 470 377 L 660 377 Z" fill="var(--cinnamon)"/>
    <path d="M560 60 C 600 150, 590 290, 440 377" fill="none" stroke="var(--rose-line)" stroke-width="3"/>
    <path d="M575 70 C 620 160, 605 300, 455 377" fill="none" stroke="var(--cream-light)" stroke-width="2"/>
  </svg>

  <div class="person">
    <h1 class="person-name">LORNA VASQUEL</h1>
    <p class="person-title">Eng. President</p>
    <p class="services">Commercial &amp; Residential General Construction Kitchen &amp; Bath Design</p>
  </div>

  <div class="contacts">
    <span class="contact-label">Phone:</span><span>555-304-7718</span>
    <span class="contact-label">Fax:</span><span>555-304-7719</span>
    <span class="contact-label">Cell:</span><span>555-862-3097</span>
    <span class="contact-label">Email:</span><span>lorna@rkbuildworks.example</span>
  </div>

  <div class="front-brand"><span class="brand-name">RK<br>Buildworks</span></div>
</section>

</body>
</html>
```